Q&J RESTORATION

I want a brochure similiar to the example i've attached.
My company name is Q&J Restoration. The website is: Q-J-Restoration.example.
The phone number is 919.555.0147.

I don't like the "yellow" being the main color of the example so I'm open to suggestions. I want something CLEAN & Simple, like our logo . This will be a bi fold brochure

```html
<!DOCTYPE html>
<html lang="en">
<head>
<meta charset="utf-8">
<title>Q&amp;J Restoration – Insurance Claim Specialist</title>
<link href="https://fonts.googleapis.com/css2?family=Poppins:wght@400;500;700&display=swap" rel="stylesheet">
<style>
  :root {
    --brand-blue: #3478e5;
    --ink: #0b0b0f;
    --paper: #ffffff;
    --haze-light: #f3f4f6;
    --haze-mid: #dfe1e6;
    --haze-deep: #cdd0d7;
  }
  * { margin: 0; padding: 0; box-sizing: border-box; }
  html, body { width: 933px; height: 1200px; overflow: hidden; background: var(--paper); }
  .cover {
    position: relative;
    width: 933px;
    height: 1200px;
    overflow: hidden;
    font-family: "Poppins", sans-serif;
    color: var(--ink);
  }
  .cover-backdrop {
    position: absolute; inset: 0;
    background:
      radial-gradient(ellipse 260px 420px at 90px 760px, rgba(170,174,184,0.45), rgba(170,174,184,0) 70%),
      radial-gradient(ellipse 420px 180px at 200px 120px, rgba(200,203,210,0.5), rgba(200,203,210,0) 75%),
      linear-gradient(200deg, var(--paper) 0%, var(--haze-light) 30%, var(--haze-mid) 70%, var(--haze-deep) 100%);
  }
  .cover-art { position: absolute; inset: 0; }
  .top-rule {
    position: absolute; left: 0; top: 0; width: 933px; height: 8px;
    background: var(--brand-blue);
  }
  .brand {
    position: absolute; left: 54px; top: 80px;
    display: flex; align-items: center; gap: 14px;
  }
  .brand-mark {
    width: 22px; height: 22px; border: 2px solid var(--ink);
  }
  .brand-name {
    font-size: 26px; font-weight: 500; letter-spacing: 3px; line-height: 1;
    color: var(--ink);
  }
  .edition-year {
    position: absolute; left: 746px; top: 50px;
    font-size: 35px; font-weight: 500; line-height: 1;
  }
  .edition-tab {
    position: absolute; left: 846px; top: 53px; width: 87px; height: 32px;
    background: var(--brand-blue);
  }
  .title-marker {
    position: absolute; left: 0; top: 216px; width: 37px; height: 32px;
    background: var(--brand-blue);
  }
  .title-lead {
    position: absolute; left: 49px; top: 206px;
    font-size: 44px; font-weight: 400; line-height: 1.2; white-space: nowrap;
  }
  .title-main {
    position: absolute; left: 46px; top: 255px;
    font-size: 98px; font-weight: 700; line-height: 1.1; letter-spacing: -3px; white-space: nowrap;
  }
  .web-band {
    position: absolute; left: 52px; top: 367px; width: 508px; height: 32px;
    background: var(--brand-blue); color: var(--paper);
    font-size: 17px; font-weight: 500; letter-spacing: 5px;
    line-height: 32px; padding-left: 14px; white-space: nowrap;
  }
  .call-line {
    position: absolute; left: 51px; top: 1052px;
    transform: rotate(-90deg); transform-origin: 0 0;
    font-size: 21px; font-weight: 400; white-space: nowrap; line-height: 21px;
  }
  .call-line strong { font-weight: 700; }
  .call-rule {
    position: absolute; left: 59px; top: 1076px; width: 2px; height: 70px;
    background: var(--brand-blue);
  }
</style>
</head>
<body>
<main class="cover">
  <div class="cover-backdrop" role="img" aria-label="Faded photo of a gutted interior under renovation with stairs and a window"></div>

  <svg class="cover-art" width="933" height="1200" viewBox="0 0 933 1200">
    <defs>
      <clipPath id="siteClip">
        <circle cx="879" cy="1006" r="635"/>
      </clipPath>
      <linearGradient id="siteBase" x1="0" y1="0" x2="0.35" y2="1">
        <stop offset="0" stop-color="#3f4552"/>
        <stop offset="0.35" stop-color="#5c6272"/>
        <stop offset="0.62" stop-color="#9298a8"/>
        <stop offset="1" stop-color="#c3c8d6"/>
      </linearGradient>
      <radialGradient id="siteWarm" cx="0.5" cy="0.5" r="0.5">
        <stop offset="0" stop-color="#d9c2ad" stop-opacity="0.75"/>
        <stop offset="1" stop-color="#d9c2ad" stop-opacity="0"/>
      </radialGradient>
      <radialGradient id="siteFloor" cx="0.5" cy="0.5" r="0.5">
        <stop offset="0" stop-color="#dfe3ee" stop-opacity="0.85"/>
        <stop offset="1" stop-color="#dfe3ee" stop-opacity="0"/>
      </radialGradient>
      <radialGradient id="siteWall" cx="0.5" cy="0.5" r="0.5">
        <stop offset="0" stop-color="#2e333e" stop-opacity="0.7"/>
        <stop offset="1" stop-color="#2e333e" stop-opacity="0"/>
      </radialGradient>
      <linearGradient id="siteFade" x1="0" y1="0" x2="1" y2="0">
        <stop offset="0" stop-color="#ffffff" stop-opacity="0.55"/>
        <stop offset="0.25" stop-color="#ffffff" stop-opacity="0"/>
      </linearGradient>
    </defs>
    <g class="site-photo" clip-path="url(#siteClip)" role="img" aria-label="Photo of a room being restored with steel props, a wheelbarrow and rubble">
      <rect x="240" y="370" width="700" height="830" fill="url(#siteBase)"/>
      <ellipse cx="500" cy="640" rx="190" ry="210" fill="url(#siteWarm)"/>
      <ellipse cx="830" cy="560" rx="200" ry="260" fill="url(#siteWall)"/>
      <ellipse cx="560" cy="1060" rx="300" ry="170" fill="url(#siteFloor)"/>
      <ellipse cx="830" cy="1050" rx="160" ry="130" fill="url(#siteFloor)"/>
      <rect x="240" y="370" width="700" height="830" fill="url(#siteFade)"/>
    </g>
    <circle class="accent-ring" cx="887" cy="1014" r="357" fill="none" stroke="#ffffff" stroke-opacity="0.8" stroke-width="11"/>
  </svg>

  <div class="top-rule"></div>
  <div class="brand">
    <span class="brand-mark"></span>
    <span class="brand-name">Q&amp;J RESTORATION</span>
  </div>
  <div class="edition-year">2023</div>
  <div class="edition-tab"></div>

  <div class="title-marker"></div>
  <h1>
    <span class="title-lead">Insurance Claim</span>
    <span class="title-main">SPECIALIST</span>
  </h1>
  <div class="web-band">WWW.Q-J-RESTORATION.EXAMPLE</div>

  <div class="call-line">Call Now : <strong>919 555 0147</strong></div>
  <div class="call-rule"></div>
</main>
</body>
</html>
```